Manuka Honey company needs a Upmarket, Luxury Website!

New Zealand, Taranaki based Manuka Honey company Rimu Vale Honey is looking for a new website, we are looking for an upmarket, luxury, serious website design. We export the highest quality quality Manuka Honey, straight from the Taranaki region.

Main export markets are Asia & Europe, also New Zealand & Australia.

Looking to have a beautiful, upmarket, serious, luxurious & graphical experience with mobile optimization in mind. Like the use of product staging/mockups

You can use copy from other websites to build the site and we will change the copy after the design is finished.

***Please include 'Honey Product' mockups in website.

*Will add illustrator files in coming days***

Feel free to make website functional in Shopify, Wordpress or WIX

Target Market(s)

Asia, Europe (main markets) New Zealand, Australia (Submarkets)

Coding

Coded - Design and coding required

Number of Pages Required

4 page

Requirements
Must have
• Home, Shop, About Us, Contact Us

Homepage to include:

Our Products
Company Video (video under construction)
What is MGO/KPS
Newsletter Opt-in

***(Not in Order)***

Please include 'Honey Product' mockups in website.
*Will add illustrator files in coming days
Nice to have
• FAQ & Partnership Inquiries (hyperlink in footer)

```html
<!DOCTYPE html>
<html lang="en">
<head>
<meta charset="utf-8">
<title>Rimu Vale Honey — Best Manuka Honey</title>
<link href="https://fonts.googleapis.com/css2?family=Jost:wght@400;500;600;700&family=Nunito+Sans:wght@400;600;700&display=swap" rel="stylesheet">
<style>
:root{
  --ink:#2b2b2b;
  --text:#4a4a4a;
  --muted:#6b6b6b;
  --gold-dark:#c7a255;
  --gold-mid:#dcc07a;
  --gold-light:#f4e8a6;
  --cream:#f6efd2;
  --sky:#dceaf3;
  --black:#050505;
  --white:#ffffff;
  --gold-grad:linear-gradient(90deg,var(--gold-dark),var(--gold-light));
}
*{box-sizing:border-box;margin:0;padding:0}
html,body{width:1200px;height:3838px;overflow:hidden}
body{position:relative;background:var(--white);font-family:"Nunito Sans",Arial,sans-serif;color:var(--text)}
.abs{position:absolute}
.heading{font-family:"Jost",Arial,sans-serif;font-weight:600;color:var(--ink);letter-spacing:5px;text-transform:uppercase}
.rule{height:4px;width:72px;background:var(--gold-grad);border-radius:2px}
.btn{display:flex;align-items:center;justify-content:center;border-radius:30px;background:var(--gold-grad);font-family:"Jost",Arial,sans-serif;font-weight:600;color:#5a4520;letter-spacing:2px;text-transform:uppercase;box-shadow:0 0 0 3px #fff,0 0 0 5px var(--gold-mid)}

/* header */
.site-header{left:0;top:0;width:1200px;height:100px;z-index:3}
.brand{left:90px;top:24px;display:flex;align-items:center;gap:14px}
.brand-dot{width:44px;height:44px;border-radius:50%;background:var(--gold-grad)}
.brand-name{font-family:"Jost",Arial,sans-serif;font-weight:400;font-size:28px;letter-spacing:4px;color:#3a3a3a;text-transform:uppercase}
.main-nav{left:596px;top:36px;display:flex;gap:0}
.main-nav a{font-family:"Nunito Sans",Arial,sans-serif;font-size:13px;color:#222;text-decoration:none;text-transform:uppercase;letter-spacing:.5px}
.main-nav a.active{font-weight:700}

/* hero */
.hero-scene{left:0;top:0;width:1200px;height:735px;background:linear-gradient(180deg,#e6f0f6 0%,#d3e4ee 35%,#cfe0ea 48%,#e9f1f5 70%,#ffffff 100%)}
.hero-title{left:0;top:135px;width:1200px;text-align:center;font-size:60px;letter-spacing:7px;font-weight:700}
.hero-sub{left:0;top:207px;width:1200px;text-align:center;font-family:"Jost",Arial,sans-serif;font-size:29px;letter-spacing:4px;color:#1f1f1f;text-transform:uppercase}
.hero-jars{left:310px;top:292px;width:548px;height:394px;border-radius:30px 30px 60px 60px;background:linear-gradient(180deg,#1b1b1b 0%,#2a2a2a 12%,#c9a02a 30%,#a55f10 70%,#d19b2a 100%)}
.arrow{top:325px}

/* mgo */
.mgo-art{left:82px;top:760px}
.mgo-title{left:619px;top:822px;font-size:35px;font-weight:700}
.mgo-rule{left:622px;top:875px}
.mgo-copy{left:623px;top:900px;width:470px;font-size:13px;line-height:22px;color:#555}
.mgo-copy p+p{margin-top:22px}
.mgo-btn{left:627px;top:1112px;width:180px;height:48px;font-size:13px}

/* products */
.products-band{left:0;top:1215px}
.products-title{left:0;top:1395px;width:1200px;text-align:center;font-size:35px;font-weight:700}
.products-rule{left:556px;top:1449px}
.card{top:1496px;width:306px;height:390px;background:var(--white);border-radius:52px;text-align:center}
.card .jar{margin:40px auto 0;width:96px;height:176px;border-radius:14px 14px 26px 26px;background:linear-gradient(180deg,#1a1a1a 0%,#1a1a1a 10%,#c38a1e 22%,#1c1c1c 40%,#1c1c1c 72%,#b77a17 82%,#d3a13b 100%)}
.card h3{font-family:"Jost",Arial,sans-serif;font-weight:500;font-size:19px;color:#222;margin-top:22px}
.card p{font-size:11px;line-height:18px;color:#666;width:220px;margin:4px auto 0}
.card .btn{margin:22px auto 0;width:150px;height:40px;font-size:10px}
.dots{left:567px;top:1942px;display:flex;gap:10px}
.dots span{width:12px;height:12px;border-radius:50%;background:#fff}
.dots span.on{background:#111}

/* video */
.video-title{left:0;top:2080px;width:1200px;text-align:center;font-size:35px;font-weight:700}
.video-rule{left:556px;top:2134px}
.video-copy{left:290px;top:2162px;width:620px;text-align:center;font-size:16px;line-height:22px;color:#555}
.video-frame{left:291px;top:2258px;width:611px;height:351px;background:radial-gradient(circle at 48% 20%,#b06a1b 0,#7a4a15 14%,#828282 28%,#7d7d7d 60%,#6c6a66 100%);box-shadow:0 10px 30px rgba(0,0,0,.18)}
.video-label{left:291px;top:2416px;width:611px;text-align:center;font-family:"Jost",Arial,sans-serif;font-weight:600;font-size:20px;letter-spacing:4px;color:#fff}
.play{left:291px;top:2549px;width:79px;height:60px;background:var(--gold-grad);display:flex;align-items:center;justify-content:center}

/* faq */
.faq-band{left:0;top:2660px}
.faq-title{left:112px;top:2820px;font-size:35px;font-weight:700;color:#fff}
.faq-rule{left:112px;top:2870px;width:76px;height:5px;background:#3a3a3a}
.faq-list{left:109px;top:2922px;width:491px}
.faq-item{border:1px solid #6a5a3a;padding:0 26px;height:48px;display:flex;align-items:center;font-size:13px;font-weight:700;color:#2a2a2a;margin-bottom:8px}
.faq-item.open{height:126px;display:block;padding-top:20px}
.faq-item.open p{font-weight:400;font-size:12px;line-height:18px;color:#6a5a3a;margin-top:16px}
.faq-art{left:663px;top:2802px}

/* footer */
.footer-band{left:0;top:3360px}
.footer-brand{left:0;top:3408px;width:1200px;text-align:center;font-family:"Jost",Arial,sans-serif;font-size:22px;letter-spacing:4px;color:var(--gold-mid);text-transform:uppercase}
.foot-col{top:3506px}
.foot-col h4{font-family:"Jost",Arial,sans-serif;font-weight:600;font-size:15px;letter-spacing:2.5px;color:#fff;text-transform:uppercase;display:inline-block;padding-bottom:6px;border-bottom:2px solid var(--gold-mid)}
.foot-col ul{list-style:none;margin-top:18px}
.foot-col li{font-size:13px;color:#fff;line-height:30px}
.foot-col .lead{font-size:13px;color:#fff;margin-top:18px}
.email{margin-top:12px;width:233px;height:34px;background:#fff;font-size:10px;color:#444;padding-left:18px;display:flex;align-items:center;letter-spacing:.5px}
.subscribe{margin-top:12px;width:233px;height:36px;background:var(--gold-grad);display:flex;align-items:center;justify-content:center;font-size:12px;font-weight:700;color:#2a2a2a;letter-spacing:.5px}
.social li{display:flex;align-items:center;gap:14px;line-height:34px}
.social i{width:12px;height:12px;border-radius:50%;border:1.5px solid #fff;display:inline-block}
.copyright{left:0;top:3778px;width:1200px;height:60px;border-top:1px solid #222;text-align:center;font-size:11px;color:#ddd;padding-top:20px}
</style>
</head>
<body>

<!-- Hero -->
<div class="abs hero-scene" role="img" aria-label="Snowy volcanic mountain reflected in a misty lake with manuka blossom sprigs"></div>
<header class="abs site-header">
  <div class="abs brand"><span class="brand-dot"></span><span class="brand-name">Rimu Vale Honey</span></div>
  <nav class="abs main-nav">
    <a class="active" href="#" style="width:115px">Home</a>
    <a href="#" style="width:115px">Shop</a>
    <a href="#" style="width:144px">About Us</a>
    <a href="#">Contact Us</a>
  </nav>
</header>
<h1 class="abs heading hero-title">Best Manuka Honey</h1>
<p class="abs hero-sub">Honey your will never taste!</p>
<div class="abs hero-jars" role="img" aria-label="Three black-labelled jars of manuka honey with black lids"></div>
<svg class="abs arrow" style="left:74px" width="26" height="50" viewBox="0 0 26 50"><polyline points="23,3 3,25 23,47" fill="none" stroke="#7a7a7a" stroke-width="3"/></svg>
<svg class="abs arrow" style="left:1100px" width="26" height="50" viewBox="0 0 26 50"><polyline points="3,3 23,25 3,47" fill="none" stroke="#7a7a7a" stroke-width="3"/></svg>

<!-- What is MGO -->
<svg class="abs mgo-art" width="480" height="474" viewBox="0 0 480 474" role="img" aria-label="Bee gathering nectar on white manuka flowers beside a honey jar">
  <defs>
    <linearGradient id="blobGold" x1="0" y1="0" x2="1" y2="1"><stop offset="0" stop-color="#efe2a9"/><stop offset="1" stop-color="#d9c07a"/></linearGradient>
    <radialGradient id="flowerPhoto" cx="0.45" cy="0.4" r="0.6"><stop offset="0" stop-color="#f4f1ea"/><stop offset="0.5" stop-color="#d8b56a"/><stop offset="1" stop-color="#8c7a55"/></radialGradient>
  </defs>
  <path d="M250 4C340 -4 440 60 470 160C495 260 450 380 350 440C250 490 120 470 55 390C0 320 -10 210 40 130C90 55 170 10 250 4Z" fill="url(#blobGold)"/>
  <circle cx="240" cy="225" r="215" fill="url(#flowerPhoto)"/>
  <rect x="310" y="240" width="128" height="230" rx="18" fill="#1d1d1d"/>
  <rect x="310" y="400" width="128" height="70" rx="18" fill="#e2b52a"/>
</svg>
<h2 class="abs heading mgo-title">What is MGO</h2>
<div class="abs rule mgo-rule"></div>
<div class="abs mgo-copy">
  <p>Lorem Ipsum is simply dummy text of the printing and typesetting industry. Lorem Ipsum has been the industry's standard dummy text ever since the 1500s, when an unknown printer took a galley of type and scrambled it to make a type specimen book. It has survived not only five centuries</p>
  <p>was popularised in the 1960s with the release of Letterfold sheets containing Lorem Ipsum passages, and more recently with desktop publishing software like Pagewright Studio including versions of Lorem Ipsum</p>
</div>
<a class="abs btn mgo-btn">Learn More</a>

<!-- Products -->
<svg class="abs products-band" width="1200" height="880" viewBox="0 0 1200 880" role="img" aria-label="Soft-focus pale manuka blossoms in cream and gold">
  <defs><linearGradient id="blossom" x1="0" y1="0" x2="1" y2="1"><stop offset="0" stop-color="#f4ead0"/><stop offset="0.5" stop-color="#faf5e4"/><stop offset="1" stop-color="#efe0ad"/></linearGradient></defs>
  <path d="M0 10C300 150 800 150 1200 0V770C900 770 500 760 0 880Z" fill="url(#blossom)"/>
</svg>
<h2 class="abs heading products-title">Our Products</h2>
<div class="abs rule products-rule" style="width:88px"></div>
<article class="abs card" style="left:107px"><div class="jar" role="img" aria-label="Jar of Mounka honey"></div><h3>Mounka Honey</h3><p>Lorem Ipsum is simply dummy text of the printing ly dummy text</p><a class="btn">Learn More</a></article>
<article class="abs card" style="left:435px;"><div class="jar" style="margin-top:36px" role="img" aria-label="Jar of Mounka honey"></div><h3 style="margin-top:18px">Mounka Honey</h3><p>Lorem Ipsum is simply dummy text of the printing ly dummy text</p><a class="btn" style="margin-top:30px">Learn More</a></article>
<article class="abs card" style="left:774px"><div class="jar" role="img" aria-label="Jar of Mounka honey"></div><h3 style="margin-top:18px">Mounka Honey</h3><p>Lorem Ipsum is simply dummy text of the printing ly dummy text</p><a class="btn" style="margin-top:26px">Learn More</a></article>
<div class="abs dots"><span class="on"></span><span></span><span></span></div>

<!-- Video -->
<h2 class="abs heading video-title">Our Company Video</h2>
<div class="abs rule video-rule"></div>
<p class="abs video-copy">Lorem Ipsum is simply dummy text of the printing and typesetting industry. Lorem Ipsum has been the industry's standard dummy.</p>
<div class="abs video-frame" role="img" aria-label="Bowl of honey with a wooden dipper beside pink manuka flowers"></div>
<p class="abs video-label">PLAY VIDEO</p>
<div class="abs play"><svg width="20" height="26" viewBox="0 0 20 26"><polygon points="0,0 20,13 0,26" fill="#000"/></svg></div>

<!-- FAQ -->
<svg class="abs faq-band" width="1200" height="800" viewBox="0 0 1200 800">
  <defs><linearGradient id="goldBand" x1="0" y1="0" x2="1" y2="1"><stop offset="0" stop-color="#f2e6b2"/><stop offset="0.5" stop-color="#ecd9a0"/><stop offset="1" stop-color="#d6b676"/></linearGradient></defs>
  <path d="M0 0C400 140 850 110 1200 5V800H0Z" fill="url(#goldBand)"/>
</svg>
<h2 class="abs heading faq-title">FAQ</h2>
<div class="abs faq-rule"></div>
<div class="abs faq-list">
  <div class="faq-item">Lorem ipsum dolor sit amet, consectetur adipiscing elit</div>
  <div class="faq-item">Sed do eiusmod tempor incididunt ut labore</div>
  <div class="faq-item">Et dolore magna aliqua. Ut enim ad minim</div>
  <div class="faq-item open">Veniam quis nostrud exercitation ullamco laboris nisi<p>Lorem Ipsum is simply dummy text of the printing and typesetting industry.<br>Lorem Ipsum has been the industry's standard dummy.</p></div>
</div>
<svg class="abs faq-art" width="460" height="480" viewBox="0 0 460 480" role="img" aria-label="Spoon of golden honey with white flowers on honeycomb and a bamboo mat">
  <defs><radialGradient id="spoonPhoto" cx="0.45" cy="0.55" r="0.6"><stop offset="0" stop-color="#f0b53a"/><stop offset="0.5" stop-color="#e8c887"/><stop offset="1" stop-color="#c99436"/></radialGradient></defs>
  <path d="M230 2C340 0 440 70 455 180C470 300 420 420 310 465C200 500 80 450 30 350C-10 260 10 140 80 70C120 30 170 4 230 2Z" fill="#f4e5b8"/>
  <circle cx="230" cy="235" r="208" fill="url(#spoonPhoto)"/>
</svg>

<!-- Footer -->
<svg class="abs footer-band" width="1200" height="480" viewBox="0 0 1200 480">
  <path d="M0 85C400 -25 800 -25 1200 85V480H0Z" fill="#050505"/>
</svg>
<div class="abs footer-brand">Rimu Vale Honey</div>
<footer>
  <div class="abs foot-col" style="left:133px"><h4>Navigation</h4><ul><li>Home</li><li>About Us</li><li>Products</li><li>Videos</li><li>Cotnact Us</li></ul></div>
  <div class="abs foot-col" style="left:350px"><h4>Useful Links</h4><ul><li>FAQ</li><li>Partnership Inquiries</li><li>Terms</li><li>Shipping &amp; Return</li><li>Cart</li></ul></div>
  <div class="abs foot-col" style="left:604px"><h4>Newsletter Sign Up</h4><p class="lead">Sign up here to stay up to date</p><div class="email">EMAIL ADDRESS</div><div class="subscribe">SUBSCRIBE</div></div>
  <div class="abs foot-col" style="left:932px"><h4>Get In Touch</h4><ul class="social"><li><i></i>Friendpage</li><li><i></i>Chirpline</li><li><i></i>Snapgrid</li><li><i></i>Workround</li></ul></div>
  <div class="abs copyright">Copyright © 2021 Rimu Vale Honey</div>
</footer>

</body>
</html>
```